Calder Vane LED - E- Commerce site

We need a website designed for an LED Billboard company that sells:
1) LED Billboards (Sales & Rental)
2) LED Gas Station lights
3) Truss Systems (Sales & Rental)
4) Sound Systems (Sales & Rental)

Attached are websites that sell similar products as Calder Vane LED. Target market is for business, property managers and event coordinators.
This site will need to be an e-commerce site where customers can purchase the product directly from the site. What I'm looking for is a design layout to start.

Conceptual Web Designs:
http://192.0.2.47:8087/index.html
http://www.pmvdisplay.example/
http://www.auralomaaudio.example/
http://www.quillmarkpanel.example/

Attached is the logo of the company: Please note that the new spelling of the logo is "Calder Vane LED" using domain " CalderVaneLED.com

Industry/Entity Type

Gas Station

Number of Pages Required

5+ page

Requirements
Must have
• 1) E-Commerce - Customers will need to be able to order product from the site.
• 2) Customers will also have the option to rent the product as well.
Nice to have
• I like the image of the attached website, that has a video clip loop
• http://www.quillmarkpanel.example/

```html
<!DOCTYPE html>
<html lang="en">
<head>
<meta charset="utf-8">
<title>Calder Vane LED</title>
<link rel="stylesheet" href="https://fonts.googleapis.com/css2?family=Open+Sans:wght@400;600;700&family=Lato:wght@400;700&display=swap">
<style>
:root{
  --pink:#e0176d;
  --red:#e32636;
  --amber:#e6a800;
  --yellow:#f7c600;
  --black:#000;
  --header:#161616;
  --ink:#1d1d1d;
  --muted:#9a9a9a;
  --grey-band:#ececec;
  --card-title:#e6e6e6;
  --white:#fff;
}
*{box-sizing:border-box;margin:0;padding:0}
html,body{width:1200px;height:2866px;overflow:hidden;background:var(--white)}
body{position:relative;font-family:"Lato",Arial,sans-serif;color:var(--ink)}
.abs{position:absolute}
h2,h3,h4,.nav,.logo-name{font-family:"Open Sans",Arial,sans-serif}

/* top bar */
.topbar{left:0;top:0;width:1200px;height:34px;background:var(--pink);display:flex;justify-content:flex-end;align-items:center;gap:34px;padding-right:100px;color:var(--white);font-size:11px;font-weight:700;letter-spacing:.3px}
.topbar span{display:flex;align-items:center;gap:6px}
.topbar i{display:inline-block;width:10px;height:10px;background:var(--white);border-radius:2px}

/* header */
.header{left:0;top:34px;width:1200px;height:102px;background:linear-gradient(#262626,#0e0e0e)}
.logo{left:130px;top:44px;display:flex;align-items:center;gap:10px}
.logo-mark{width:76px;height:76px;border-radius:50%;background:var(--pink)}
.logo-name{color:var(--yellow);font-weight:700;font-size:26px;line-height:1}
.search{left:576px;top:66px;width:196px;height:36px;border:1.5px solid #bbb;border-radius:18px;color:#aaa;font-size:12px;padding:10px 16px}
.search svg{position:absolute;right:12px;top:9px}
.phone{left:792px;top:66px;display:flex;align-items:center;gap:10px;color:var(--white);font-weight:700;font-size:17px}
.phone .ring{width:38px;height:38px;border:1.5px solid #bbb;border-radius:50%;display:flex;align-items:center;justify-content:center}
.cart{left:950px;top:70px;color:var(--white);display:flex;gap:10px;align-items:center;font-size:10px;line-height:1.5}
.cart b{font-weight:700}

/* nav */
.nav{left:86px;top:134px;width:1028px;height:44px;background:var(--white);border-radius:22px;display:flex;align-items:center;font-size:14px;color:var(--ink);z-index:2;overflow:hidden}
.nav a{height:44px;display:flex;align-items:center;padding:0 26px;border-right:1px solid #ddd;text-decoration:none;color:inherit}
.nav a:last-child{border:0}
.nav a.active{background:var(--yellow);font-weight:700;margin-left:20px}

/* hero */
.hero{left:0;top:136px;width:1200px;height:466px;background:linear-gradient(110deg,#3a0f14 0%,#8a1c2a 20%,#231a33 45%,#5a2a1e 65%,#1b1b2a 85%,#6a4a5a 100%)}
.hero-banner{left:130px;top:355px;width:444px;height:110px;background:rgba(170,170,170,.55);clip-path:polygon(0 0,88% 0,100% 50%,88% 100%,0 100%)}
.hero-title{left:153px;top:376px;font-family:"Open Sans",sans-serif;font-weight:700;font-size:38px;color:#111}
.hero-btn{left:150px;top:437px;width:114px;height:28px;background:var(--red);color:var(--white);font-size:18px;font-weight:700;display:flex;align-items:center;justify-content:center}
.dots{left:578px;top:552px;display:flex;gap:8px}
.dots i{width:9px;height:9px;border-radius:50%;background:rgba(255,255,255,.55)}
.dots i:first-child{background:var(--white)}

/* section titles */
.sec-title{width:1200px;left:0;text-align:center;font-weight:700;font-size:34px;color:#111}
.divider{left:480px;width:240px;height:1px;background:#bbb}
.divider::after{content:"";position:absolute;left:116px;top:-4px;width:8px;height:8px;border-radius:50%;background:#bbb}
.lede{left:160px;top:735px;width:880px;text-align:center;font-size:15px;line-height:27px;color:#222}

/* what we do grid */
.services{left:130px;top:808px;width:938px;height:432px;display:grid;grid-template-columns:1fr 1fr;grid-template-rows:1fr 1fr;gap:3px;background:#000}
.tile{position:relative;display:flex;flex-direction:column;align-items:center;justify-content:center;gap:14px}
.tile::before{content:"";position:absolute;inset:6px;border:1px dashed rgba(255,255,255,.45)}
.tile h3{position:relative;color:var(--white);font-size:30px;font-weight:600}
.tile .more{position:relative;border:1.5px solid var(--white);color:var(--white);font-size:12px;font-weight:700;padding:6px 20px}
.t1{background:linear-gradient(135deg,#3b2f3e,#7a3c2c 60%,#233)}
.t2{background:linear-gradient(160deg,#1d2230,#5a6270 55%,#10131a)}
.t3{background:linear-gradient(135deg,#2a1030,#5a1a3c 50%,#150a20)}
.t4{background:linear-gradient(135deg,#3a4a55,#8a8a8e 50%,#2a343e)}

/* product sections */
.band-grey{left:0;width:1200px;background:var(--grey-band)}
.card{width:264px;height:318px;background:var(--white);border:1px solid #ddd;border-radius:6px;box-shadow:0 1px 4px rgba(0,0,0,.12);overflow:hidden}
.card .pic{height:168px;margin:0 auto}
.card h4{height:34px;background:var(--card-title);display:flex;align-items:center;justify-content:center;font-size:15px;font-weight:700;color:#111}
.card p{text-align:center;font-size:12.5px;line-height:18px;color:var(--muted);padding:14px 24px 0}
.btns{display:flex;justify-content:center;gap:14px;margin-top:14px}
.btns span{width:94px;height:26px;display:flex;align-items:center;justify-content:center;color:var(--white);font-size:12.5px;font-weight:700}
.buy{background:var(--red)}
.rent{background:var(--amber)}

/* features */
.feature{top:2354px;width:300px;height:124px;background:var(--white);border-top:4px solid var(--red);border-radius:6px 6px 0 0;box-shadow:0 1px 4px rgba(0,0,0,.12);padding:12px 16px}
.feature h4{font-size:18px;font-weight:700;color:#111}
.feature .sub{font-size:12px;font-weight:700;color:#333;margin-top:10px}
.feature p{font-size:13px;line-height:20px;color:#333;margin-top:4px;width:230px}
.feature svg{position:absolute;right:18px;top:14px}

/* footer */
.footer{left:0;top:2515px;width:1200px;height:351px;background:var(--black);color:var(--white)}
.f-logo{left:134px;top:2546px;display:flex;align-items:center;gap:10px}
.f-logo .logo-mark{width:72px;height:72px}
.f-about{left:136px;top:2646px;width:330px;font-size:15px;line-height:24px}
.f-head{font-family:"Open Sans",sans-serif;font-weight:600;font-size:21px}
.links{left:520px;top:2600px;list-style:none;font-size:13px;line-height:23.5px}
.links li::before{content:"›";color:var(--pink);font-weight:700;margin-right:10px}
.contact{left:716px;top:2606px;font-size:13px;line-height:18px;width:180px}
.contact div{display:flex;gap:12px;margin-bottom:12px}
.contact svg{flex:none;margin-top:2px}
.contact b{font-weight:700}
.social{left:1002px;top:2600px;display:flex;flex-direction:column;gap:13px}
.social i{width:34px;height:34px;border:1.5px solid var(--pink);border-radius:50%;display:block;position:relative}
.social i::after{content:"";position:absolute;left:12px;top:12px;width:8px;height:8px;border-radius:50%;background:var(--pink)}
.copy{left:132px;top:2834px;font-size:12px}
.pay{left:784px;top:2832px;display:flex;gap:6px}
.pay i{width:36px;height:20px;background:#d9d9d9;border-radius:2px;display:block}
</style>
</head>
<body>

<div class="abs topbar">
  <span><i></i>MY ACCOUNT</span>
  <span><i></i>MY WISHLIST</span>
  <span><i></i>CHECKOUT</span>
  <span><i></i>LOG IN / REGISTER</span>
</div>

<header class="abs header"></header>
<div class="abs logo"><div class="logo-mark"></div><div class="logo-name">Calder Vane LED</div></div>
<div class="abs search">Search
  <svg width="16" height="16" viewBox="0 0 16 16"><circle cx="6.5" cy="6.5" r="5" fill="none" stroke="#fff" stroke-width="2"/><path d="M10.5 10.5L15 15" stroke="#fff" stroke-width="2.4"/></svg>
</div>
<div class="abs phone"><span class="ring"><svg width="16" height="16" viewBox="0 0 24 24"><path fill="#fff" d="M6.6 10.8a15 15 0 006.6 6.6l2.2-2.2c.3-.3.7-.4 1-.2 1.1.4 2.3.6 3.6.6.6 0 1 .4 1 1V20c0 .6-.4 1-1 1A17 17 0 013 4c0-.6.4-1 1-1h3.5c.6 0 1 .4 1 1 0 1.3.2 2.5.6 3.6.1.3 0 .7-.2 1z"/></svg></span>123-456-7890</div>
<div class="abs cart">
  <svg width="24" height="24" viewBox="0 0 24 24"><path fill="#fff" d="M5 8h14l-1 13H6z"/><path d="M9 8V6a3 3 0 016 0v2" fill="none" stroke="#fff" stroke-width="2"/></svg>
  <div><b>SHOPPING CART</b><br>0 item(s) ⌄</div>
</div>

<nav class="abs nav">
  <a class="active">Home</a>
  <a>LED lights Systems</a>
  <a>Truss Systems</a>
  <a>Sound Systems</a>
  <a>Service and Support</a>
  <a>About</a>
  <a>Contact US</a>
</nav>

<div class="abs hero" role="img" aria-label="Night city street lined with glowing LED billboards"></div>
<div class="abs hero-banner"></div>
<div class="abs hero-title">Light Up Your World</div>
<div class="abs hero-btn">Call Now</div>
<div class="abs dots"><i></i><i></i><i></i></div>

<h2 class="abs sec-title" style="top:636px">What We Do</h2>
<div class="abs divider" style="top:707px"></div>
<p class="abs lede">Lorem ipsum dolor sit amet, consectetuer adipiscing elit, sed diam nonummy nibh euismod tincidunt ut laoreet dolore magna aliquam erat volutpat. Ut wisi enim ad minim veniam, quis nostrud exerci tation ullamcorper suscipit lobortis nisl ut aliquip ex ea.</p>

<div class="abs services">
  <div class="tile t1" role="img" aria-label="Busy city square with LED billboards at night"><h3>LED Billboards</h3><span class="more">Learn More</span></div>
  <div class="tile t2" role="img" aria-label="Gas station canopy lit by LED lights"><h3>LED Gas Station Lights</h3><span class="more">Learn More</span></div>
  <div class="tile t3" role="img" aria-label="Stage truss rig under purple lighting"><h3>Truss Systems</h3><span class="more">Learn More</span></div>
  <div class="tile t4" role="img" aria-label="Hands on a sound mixing console"><h3>Sound Systems</h3><span class="more">Learn More</span></div>
</div>

<div class="abs band-grey" style="top:1290px;height:531px"></div>
<h2 class="abs sec-title" style="top:1311px">Popular Products</h2>
<div class="abs divider" style="top:1378px"></div>

<div class="abs card" style="left:160px;top:1410px">
  <div class="pic" role="img" aria-label="Round recessed LED panel light" style="background:radial-gradient(circle at 50% 55%,#f2f2f2 0 30%,#d8d8d8 31% 36%,#fff 37%)"></div>
  <h4>30W-LED Panel Light</h4>
  <p>Pellentesque in rhoncus? In nec cursus et, magna odio? Enim, magnis,</p>
  <div class="btns"><span class="buy">Buy Now</span><span class="rent">On Rent</span></div>
</div>
<div class="abs card" style="left:468px;top:1410px">
  <div class="pic" role="img" aria-label="Two LED tube lights" style="background:linear-gradient(160deg,#fff 20%,#e4e6ea 35%,#fff 45%,#e4e6ea 60%,#fff 75%)"></div>
  <h4>20W-T8-LED Tube-UL</h4>
  <p>Pellentesque in rhoncus? In nec cursus et, magna odio? Enim, magnis,</p>
  <div class="btns"><span class="buy">Buy Now</span><span class="rent">On Rent</span></div>
</div>
<div class="abs card" style="left:774px;top:1410px">
  <div class="pic" role="img" aria-label="Stage wash light with barn doors" style="background:radial-gradient(circle at 50% 50%,#3a3a3a 0 22%,#fff 40%)"></div>
  <h4>DJ Truss arch</h4>
  <p>Pellentesque in rhoncus? In nec cursus et, magna odio? Enim, magnis,</p>
  <div class="btns"><span class="buy">Buy Now</span><span class="rent">On Rent</span></div>
</div>

<h2 class="abs sec-title" style="top:1848px">Latest Products</h2>
<div class="abs divider" style="top:1915px"></div>

<div class="abs card" style="left:160px;top:1949px">
  <div class="pic" role="img" aria-label="Four-deck DJ controller" style="background:radial-gradient(ellipse at 50% 55%,#2a2a2a 0 35%,#fff 55%)"></div>
  <h4>Orvane MixStation Quad</h4>
  <p>Pellentesque in rhoncus? In nec cursus et, magna odio? Enim, magnis,</p>
  <div class="btns"><span class="buy">Buy Now</span><span class="rent">On Rent</span></div>
</div>
<div class="abs card" style="left:468px;top:1949px">
  <div class="pic" role="img" aria-label="Square LED panel light" style="background:radial-gradient(ellipse at 50% 50%,#eef0f2 0 28%,#d6d8dc 30% 33%,#fff 36%)"></div>
  <h4>30W-LED Panel Light</h4>
  <p>Pellentesque in rhoncus? In nec cursus et, magna odio? Enim, magnis,</p>
  <div class="btns"><span class="buy">Buy Now</span><span class="rent">On Rent</span></div>
</div>
<div class="abs card" style="left:774px;top:1949px">
  <div class="pic" role="img" aria-label="Slim T5 LED batten fixture" style="background:linear-gradient(170deg,#fff 30%,#e2e4e8 42%,#f6f6f6 50%,#fff 62%)"></div>
  <h4>Lumeline T5 LED</h4>
  <p>Pellentesque in rhoncus? In nec cursus et, magna odio? Enim, magnis,</p>
  <div class="btns"><span class="buy">Buy Now</span><span class="rent">On Rent</span></div>
</div>

<div class="abs band-grey" style="top:2322px;height:193px;background:#dcdcdc"></div>
<div class="abs feature" style="left:124px">
  <h4>Free Home shipping!</h4><div class="sub">This is a snappy sub-title</div>
  <p>Lorem ipsum dolor sit amet, consectetur adipisicing, Neque beatae.</p>
  <svg width="62" height="44" viewBox="0 0 62 44"><rect x="2" y="6" width="36" height="26" rx="2" fill="#e32636"/><path d="M38 14h12l8 10v8H38z" fill="#e32636"/><circle cx="14" cy="36" r="5" fill="#e32636"/><circle cx="48" cy="36" r="5" fill="#e32636"/><text x="20" y="24" fill="#fff" font-size="10" font-weight="700" text-anchor="middle" font-family="Open Sans,sans-serif">FREE</text></svg>
</div>
<div class="abs feature" style="left:445px">
  <h4>We're now global!</h4><div class="sub">This is a snappy sub-title</div>
  <p>Lorem ipsum dolor sit amet, consectetur adipisicing, Neque beatae.</p>
  <svg width="52" height="52" viewBox="0 0 52 52" fill="none" stroke="#e32636" stroke-width="3"><circle cx="26" cy="26" r="22"/><ellipse cx="26" cy="26" rx="10" ry="22"/><path d="M4 26h44M8 14h36M8 38h36"/></svg>
</div>
<div class="abs feature" style="left:764px">
  <h4>Lowest price guarantee!</h4><div class="sub">This is a snappy sub-title</div>
  <p>Lorem ipsum dolor sit amet, consectetur adipisicing, Neque beatae.</p>
  <svg width="50" height="60" viewBox="0 0 50 60"><path d="M18 4h22l6 8-14 44-26-10 14-42z" fill="#e32636" transform="rotate(15 25 30)"/><circle cx="32" cy="14" r="3" fill="#fff"/><text x="26" y="40" fill="#fff" font-size="16" font-weight="700" text-anchor="middle" font-family="Open Sans,sans-serif">$</text></svg>
</div>

<footer class="abs footer"></footer>
<div class="abs f-logo"><div class="logo-mark"></div><div class="logo-name">Calder Vane LED</div></div>
<p class="abs f-about">Lorem ipsum dolor sit amet, consectetuer elit, sed diam nonummy nibh euismod tincidunt ut laoreet dolore magna aliquam erat volutpat. Ut wisi enim ad minim veniam, quis nostrud exerci tation ullamcorper suscipit lobortis nisl ut aliquip ex ea commodo</p>

<h4 class="abs f-head" style="left:516px;top:2554px;color:#fff">Useful Links</h4>
<ul class="abs links" style="color:#fff">
  <li>Home</li><li>LED lights Systems</li><li>Truss Systems</li><li>Sound Systems</li><li>Service and Support</li><li>About</li><li>Contact US</li>
</ul>

<h4 class="abs f-head" style="left:714px;top:2554px;color:#fff">Contact</h4>
<div class="abs contact" style="color:#fff">
  <div><svg width="12" height="16" viewBox="0 0 12 16"><path d="M6 0a6 6 0 016 6c0 4-6 10-6 10S0 10 0 6a6 6 0 016-6z" fill="#e0176d"/><circle cx="6" cy="6" r="2" fill="#000"/></svg><span>123, Lorem ipsum dolor sit nil amet, consectetuer adipiscingt.</span></div>
  <div><svg width="14" height="14" viewBox="0 0 24 24"><path fill="#e0176d" d="M6.6 10.8a15 15 0 006.6 6.6l2.2-2.2c.3-.3.7-.4 1-.2 1.1.4 2.3.6 3.6.6.6 0 1 .4 1 1V20c0 .6-.4 1-1 1A17 17 0 013 4c0-.6.4-1 1-1h3.5c.6 0 1 .4 1 1 0 1.3.2 2.5.6 3.6.1.3 0 .7-.2 1z"/></svg><b>123-456-7890</b></div>
  <div><svg width="14" height="14" viewBox="0 0 24 24"><path fill="#e0176d" d="M6.6 10.8a15 15 0 006.6 6.6l2.2-2.2c.3-.3.7-.4 1-.2 1.1.4 2.3.6 3.6.6.6 0 1 .4 1 1V20c0 .6-.4 1-1 1A17 17 0 013 4c0-.6.4-1 1-1h3.5c.6 0 1 .4 1 1 0 1.3.2 2.5.6 3.6.1.3 0 .7-.2 1z"/></svg><b>123-456-7890</b></div>
  <div><svg width="14" height="11" viewBox="0 0 14 11"><rect width="14" height="11" rx="1" fill="#e0176d"/><path d="M0 1l7 5 7-5" stroke="#000" fill="none"/></svg><span>info@caldervaneled.com</span></div>
</div>

<h4 class="abs f-head" style="left:969px;top:2554px;color:#fff">Follow Us</h4>
<div class="abs social"><i></i><i></i><i></i><i></i></div>

<div class="abs copy" style="color:#fff">Copyright © 2016 - Calder Vane LED, All Rights Reserved</div>
<div class="abs pay"><i></i><i></i><i></i><i></i><i></i><i></i><i></i></div>

</body>
</html>
```